Etiketten-Design für Rotwein
Zielgruppe
Weinkellerei aus Baden (Deutschland) mit Fokus im Lebensmittelhandel in Deutschland
Aufgabenstellung
Wir suchen ein Frontetikett für einen modernen badischen Rotwein (Cuvée Lumen) mit dem Namen 'Die stille Seite vom Hang'
Aus dem Etikett soll hervorgehen, dass es sich nicht um einen klassischen, leichten deutschen Rotwein handelt, sondern um einen kräftigen, gehaltvollen, mediterran anmutenden Rotwein mit purpurroter Farbe und vollmundigem, nachhaltigem Geschmack. (Geschmacksrichtung feinherb)
Zielgruppe Discount-Kunden, Männlich/Weiblich, Alter: 25-60 Jahre, wird für unter € 5,-/Fl. verkauft.
Weinbeschreibung:
Farbe: Ein wunderschönes tiefdunkles purpurrot mit violetten Reflexen
Duft: In der Nase zeigen sich Aromen nach Waldbeeren, sowie Anklänge von Rauch, Röstaromen, Nelke, etwas Vanille und dunkle Schokolade
Geschmack: Geschmacklich füllig und kraftvoll, Brombeeraromen und schön eingebundenen Tanninen. Langanhaltend intensiv im Abgang.
Anforderungen Etikett:
Maße: Höhe max. 120mm/Breite max. 80mm (darf auch kleiner oder quadratisch sein)
SK Etikett, Naturstruktur bis 90g (m²) (Ein - oder zweiteilig)
Eine figürliche Etikettenkontur ist möglich, es wird aber am rechten Etikettenrand eine gerade Spendekante benötigt um das Etikett maschinell verarbeiten zu können.
Als Flasche wird eine 0,75 L Bordeauxflasche (Farbe: grün) eingesetzt.
Verschluss: Longcap
Mögliche Veredelungen: Quelllack, Prägungen, Heissfolie, Glanzlack
Pflichtangaben:
Die stille Seite vom Hang

```html
<!DOCTYPE html>
<html lang="de">
<head>
<meta charset="utf-8">
<title>Die stille Seite vom Hang – Frontetikett</title>
<link rel="stylesheet" href="https://fonts.googleapis.com/css2?family=Cinzel:wght@600;700&family=Josefin+Sans:wght@300;400&display=swap">
<style>
  :root {
    --page-bg: #e6e1dc;
    --label-top: #8a4f98;
    --label-mid: #9a52d8;
    --label-low: #7a3be0;
    --label-deep: #5a2a9a;
    --ridge: #4e3060;
    --field: #6a3aa8;
    --ink-light: #ffffff;
    --shadow: rgba(40, 20, 50, 0.35);
  }
  * { box-sizing: border-box; margin: 0; padding: 0; }
  html, body {
    width: 1200px;
    height: 2337px;
    overflow: hidden;
    background: var(--page-bg);
  }
  .canvas {
    position: relative;
    width: 1200px;
    height: 2337px;
  }
  .label {
    position: absolute;
    left: 100px;
    top: 482px;
    width: 1000px;
    height: 1373px;
    overflow: hidden;
    box-shadow: 10px 12px 18px var(--shadow);
    color: var(--ink-light);
  }
  .label-backdrop {
    position: absolute;
    inset: 0;
    background:
      radial-gradient(ellipse 60% 35% at 75% 30%, rgba(200, 110, 200, 0.35), transparent 70%),
      radial-gradient(ellipse 55% 30% at 20% 60%, rgba(170, 90, 230, 0.35), transparent 70%),
      linear-gradient(180deg, var(--label-top) 0%, var(--label-mid) 45%, var(--label-low) 78%, var(--label-deep) 100%);
  }
  .landscape {
    position: absolute;
    left: 0;
    right: 0;
    bottom: 0;
    height: 245px;
    background: linear-gradient(180deg, var(--ridge) 0%, var(--ridge) 14%, var(--field) 30%, var(--label-deep) 100%);
    opacity: 0.85;
  }
  .title {
    position: absolute;
    left: 156px;
    top: 262px;
    font-family: "Cinzel", serif;
    font-weight: 700;
    font-size: 112px;
    line-height: 133px;
    letter-spacing: 0.005em;
  }
  .title span { display: block; white-space: nowrap; }
  .rule {
    position: absolute;
    left: 158px;
    top: 858px;
    width: 321px;
    height: 4px;
    background: var(--ink-light);
  }
  .variety, .vintage, .volume {
    position: absolute;
    font-family: "Josefin Sans", sans-serif;
    font-weight: 300;
    white-space: nowrap;
  }
  .variety {
    left: 158px;
    top: 908px;
    font-size: 50px;
    letter-spacing: 0.14em;
    text-transform: uppercase;
  }
  .vintage {
    left: 158px;
    top: 994px;
    font-size: 50px;
    letter-spacing: 0.1em;
  }
  .volume {
    right: 80px;
    top: 1262px;
    font-size: 42px;
    letter-spacing: 0.12em;
  }
</style>
</head>
<body>
<main class="canvas">
  <section class="label" aria-label="Frontetikett Die stille Seite vom Hang">
    <div class="label-backdrop" role="img" aria-label="Violetter Farbverlauf mit gerasterten, geschwungenen Bändern"></div>
    <div class="landscape" role="img" aria-label="Gemalte Landschaft mit Horizont und Baumreihe in Violett"></div>
    <h1 class="title">
      <span>Die stille</span>
      <span>Seite</span>
      <span>vom</span>
      <span>Hang</span>
    </h1>
    <div class="rule"></div>
    <p class="variety">Cuvée Lumen</p>
    <p class="vintage">2021</p>
    <p class="volume">0,75 L</p>
  </section>
</main>
</body>
</html>
```